BRIGHT RIVER POWER.

I'd like my business logo.
contact name: Dennis Halvorsen
phone:0438759164
email: info@brightriverpower.net.au
website: www.brightriverpower.net.au

services:
solar
battery storage
LED lighting
energy saving solutions
general electrical
I'd like the design to look professional

Target Market(s)

Everyone

Industry/Entity Type

Business

Contact Information for Business Card

as described above

Requirements
Must have
• Id like the colours and the design to work well with my logo.

```html
<!DOCTYPE html>
<html lang="en">
<head>
<meta charset="utf-8">
<title>Bright River Power – Business Card</title>
<link rel="stylesheet" href="https://fonts.googleapis.com/css2?family=Source+Sans+3:wght@400;600&display=swap">
<style>
  :root {
    --backdrop: #e6e6e4;
    --card: #ffffff;
    --green: #8cc63e;
    --green-text: #55b447;
    --orange: #f8a51b;
    --orange-text: #f29a1c;
    --white: #ffffff;
  }
  html, body {
    margin: 0;
    width: 1200px;
    height: 900px;
    overflow: hidden;
    background: var(--backdrop);
    font-family: "Source Sans 3", "Myriad Pro", Arial, sans-serif;
  }
  .business-card {
    position: absolute;
    left: 120px;
    top: 153px;
    width: 960px;
    height: 594px;
    background: var(--card);
    overflow: hidden;
    box-shadow: 0 6px 24px rgba(0,0,0,0.12);
  }
  .brand {
    position: absolute;
    left: 50px;
    top: 70px;
    display: flex;
    align-items: center;
    gap: 22px;
  }
  .brand-dot {
    width: 62px;
    height: 62px;
    border-radius: 50%;
    background: var(--orange);
    flex: none;
  }
  .brand-name {
    font-size: 70px;
    font-weight: 600;
    color: var(--green-text);
    letter-spacing: 1px;
    line-height: 1;
    white-space: nowrap;
  }
  .contact-name {
    position: absolute;
    left: 97px;
    top: 272px;
    margin: 0;
    font-size: 34px;
    font-weight: 600;
    color: var(--orange-text);
  }
  .contact-list {
    position: absolute;
    left: 105px;
    top: 340px;
    margin: 0;
    padding: 0;
    list-style: none;
  }
  .contact-list li {
    display: flex;
    align-items: center;
    height: 36px;
    font-size: 27px;
    color: var(--green-text);
  }
  .contact-icon {
    width: 18px;
    height: 18px;
    margin-right: 14px;
    flex: none;
  }
  .band-green {
    position: absolute;
    left: 0;
    top: 483px;
    width: 100%;
    height: 25px;
    background: var(--green);
  }
  .band-services {
    position: absolute;
    left: 0;
    top: 508px;
    width: 100%;
    height: 86px;
    background: var(--orange);
    display: flex;
    align-items: center;
    justify-content: center;
  }
  .service {
    font-size: 22px;
    color: var(--white);
    white-space: nowrap;
  }
  .service + .service::before {
    content: "";
    display: inline-block;
    width: 10px;
    height: 10px;
    border-radius: 50%;
    background: var(--white);
    margin: 0 11px 0 17px;
    vertical-align: middle;
  }
</style>
</head>
<body>
  <div class="business-card">
    <div class="brand">
      <span class="brand-dot"></span>
      <span class="brand-name">BRIGHT RIVER POWER</span>
    </div>

    <h1 class="contact-name">Dennis Halvorsen</h1>
    <ul class="contact-list">
      <li>
        <svg class="contact-icon" viewBox="0 0 24 24" aria-hidden="true"><path fill="#f8a51b" d="M6.6 10.8a15.1 15.1 0 0 0 6.6 6.6l2.2-2.2c.3-.3.7-.4 1-.2 1.1.4 2.3.6 3.6.6.6 0 1 .4 1 1V20c0 .6-.4 1-1 1A17 17 0 0 1 3 4c0-.6.4-1 1-1h3.5c.6 0 1 .4 1 1 0 1.3.2 2.5.6 3.6.1.3 0 .7-.2 1z"/></svg>
        <span>0438759164</span>
      </li>
      <li>
        <svg class="contact-icon" viewBox="0 0 24 24" aria-hidden="true"><path fill="#f8a51b" d="M2 5h20v14H2z"/><path fill="none" stroke="#fff" stroke-width="2" d="M2 6l10 7 10-7"/></svg>
        <span>info@brightriverpower.net.au</span>
      </li>
      <li>
        <svg class="contact-icon" viewBox="0 0 24 24" aria-hidden="true"><circle cx="12" cy="12" r="10" fill="#f8a51b"/><path fill="none" stroke="#fff" stroke-width="1.6" d="M2 12h20M12 2c3 3 3 17 0 20M12 2c-3 3-3 17 0 20"/></svg>
        <span>www.brightriverpower.net.au</span>
      </li>
    </ul>

    <div class="band-green"></div>
    <div class="band-services">
      <span class="service">Solar</span>
      <span class="service">Battery Storage</span>
      <span class="service">LED Lighting</span>
      <span class="service">Energy Saving Solutions</span>
      <span class="service">General Electrical</span>
    </div>
  </div>
</body>
</html>
```